BUSINESS CARD - HALLORAN FIELD SERVICES

I would like to create a business card for my fertilizer spreading business. I would like to incorporate my existing logo and also a description of the services offered. The business card will be given to farmers so must be kept simple but effective. It will also be left in stores so much also be eye catching in order to stand out from other cards.

Target Market(s)

FARMERS

Requirements
Must have
• FRONT OF CARD = EXISTING LOGO + "CUSTOMISED SPREADING" below the logo

REAR Of CARD = SERVICES OFFERED AND CONTACT DETAILS

- Bulk fertilizer including Lime, Gypsum, Manure & Compost
- Granular fertilizer including Single Super, Urea, Gran-am, & Custom Blends
- Modern equipment - Autosteer & Variable Rate Capable
- Friendly & Reliable Service
- Contact Gus: 0417 552 308
Nice to have
• utilize same color scheme as existing logo

```html
<!DOCTYPE html>
<html lang="en">
<head>
<meta charset="utf-8">
<title>Halloran Field Services – Business Card</title>
<link href="https://fonts.googleapis.com/css2?family=Questrial&display=swap" rel="stylesheet">
<style>
  :root {
    --stage: #e4e4e2;
    --paper: #ffffff;
    --ink: #4a4a4a;
    --orange: #f39323;
    --charcoal: #4b4b4d;
  }
  * { box-sizing: border-box; margin: 0; padding: 0; }
  html, body { width: 1200px; height: 900px; overflow: hidden; }
  body {
    background: var(--stage);
    font-family: "Questrial", "Century Gothic", sans-serif;
    color: var(--ink);
    display: flex;
    flex-direction: column;
    align-items: center;
    justify-content: center;
    gap: 44px;
  }
  .card {
    position: relative;
    width: 660px;
    height: 378px;
    background: var(--paper);
    box-shadow: 0 6px 20px rgba(0,0,0,.18);
    overflow: hidden;
  }

  /* Rear of card */
  .card-rear .services {
    position: absolute;
    top: 40px; left: 0; right: 0;
    text-align: center;
  }
  .services-title {
    color: var(--orange);
    font-size: 21px;
    font-weight: 400;
    margin-bottom: 14px;
  }
  .services-list { list-style: none; }
  .services-list li {
    font-size: 17.5px;
    line-height: 30px;
    color: var(--ink);
  }
  .contact {
    margin-top: 16px;
    color: var(--orange);
    font-size: 22px;
    letter-spacing: 1px;
    display: flex;
    justify-content: center;
    align-items: center;
    gap: 10px;
  }
  .contact svg { width: 28px; height: 22px; }
  .rear-band {
    position: absolute;
    left: 0; right: 0; bottom: 0;
    height: 48px;
    background: var(--orange);
  }
  .rear-livestock {
    position: absolute;
    right: 24px; bottom: 48px;
    width: 150px; height: 52px;
    background: var(--orange);
    border-radius: 10px 16px 0 0;
  }

  /* Front of card */
  .front-band {
    position: absolute;
    left: 0; right: 0; bottom: 0;
    height: 74px;
    background: var(--charcoal);
  }
  .front-livestock {
    position: absolute;
    left: 34px; bottom: 74px;
    width: 170px; height: 62px;
    background: var(--charcoal);
    border-radius: 12px 18px 0 0;
  }
  .brand {
    position: absolute;
    top: 54px; right: 56px;
    width: 300px;
    text-align: center;
  }
  .brand-mark {
    display: block;
    margin: 0 auto 14px;
    width: 96px; height: 96px;
    border-radius: 50%;
    border: 7px solid var(--charcoal);
  }
  .brand-name {
    font-size: 27px;
    line-height: 1.15;
    color: var(--charcoal);
    letter-spacing: .5px;
  }
  .brand-rule {
    height: 2px;
    background: var(--orange);
    margin: 10px 20px 10px;
  }
  .brand-tagline {
    font-size: 21px;
    color: var(--ink);
    letter-spacing: 1px;
  }
</style>
</head>
<body>

  <section class="card card-rear" aria-label="Rear of card">
    <div class="services">
      <h2 class="services-title">Services Offered And Contact Details</h2>
      <ul class="services-list">
        <li>Bulk fertilizer including Lime, Gypsum, Manure &amp; Compost</li>
        <li>Granular fertilizer including Single Super</li>
        <li>Urea, Gran-am, &amp; Custom Blends</li>
        <li>Modern equipment - Autosteer &amp; Variable Rate Capable</li>
        <li>Friendly &amp; Reliable Service</li>
      </ul>
      <p class="contact">
        <svg viewBox="0 0 28 22" aria-hidden="true">
          <path d="M2 7 Q14 -1 26 7 L23 10 L19 8 L19 5 Q14 3 9 5 L9 8 L5 10 Z" fill="currentColor"/>
          <path d="M7 11 L21 11 L24 20 L4 20 Z" fill="currentColor"/>
          <circle cx="14" cy="15.5" r="2.6" fill="#fff"/>
        </svg>
        <span>0417 552 308</span>
      </p>
    </div>
    <div class="rear-livestock" role="img" aria-label="Silhouette of a cow and a sheep standing on grass"></div>
    <div class="rear-band"></div>
  </section>

  <section class="card card-front" aria-label="Front of card">
    <div class="brand">
      <span class="brand-mark" aria-hidden="true"></span>
      <p class="brand-name">Halloran Field Services</p>
      <div class="brand-rule"></div>
      <p class="brand-tagline">Customised Spreading</p>
    </div>
    <div class="front-livestock" role="img" aria-label="Silhouette of a cow and a sheep standing on grass"></div>
    <div class="front-band"></div>
  </section>

</body>
</html>
```